Redesign Digital Lending Mobile App - Android/ Flutter

Want to re-theme an existing Digital Lending Mobile app to simplify customer journeys, as well as uplift the UI.

Most users will have small screen phones so the design needs to take that into consideration while also adapting to those with larger devices, like admins with Tablets.

Have already laid out customer journeys on Figma with guidance on how the flow of the app should be. https://www.plankora.example/board/q4ZtRm81KdWe7YhXcvBnaL/LoomKit?frame-id=3-5182&s=Jk2pQwEr7TyUi-9

Video capture of current app: https://vaultbin.example/clip/7Hx3LmQp9RtZw2KcVn4YsBd8EfGj1/play
https://vaultbin.example/clip/4PsWq8ZnTk2LrXy6MbJc3VhGd9FeA/play

The documented views for Web are also here https://docshelf.example/open?ref=3B8F2204AD7C91E5!tk8d1f6a2c4e7b90d3f5a1c8e2b6d4f9a07&cid=3b8f2204ad7c91e5&kind=file%2Cdocx&wdo=2

Target Market(s)

Kenya, Tanzania, Uganda - Africa

Industry/Entity Type

Fintech

Requirements
Must have
• Responsive for diff screens, esp. in context of smaller screen smartphone
Nice to have
• Thematic components to ensure new views can easily be adapted to these themse

```html
<!DOCTYPE html>
<html lang="en">
<head>
<meta charset="utf-8">
<title>LoomKit – Lending App Screens</title>
<link rel="stylesheet" href="https://fonts.googleapis.com/css2?family=Poppins:wght@400;500;600;700;800&display=swap">
<style>
:root{
  --page:#e6e5e6;
  --white:#ffffff;
  --ink:#1f1f1f;
  --text:#333333;
  --muted:#555555;
  --soft:#777777;
  --blue:#2f6fc4;
  --blue-bright:#0b8fe0;
  --green:#4a9a6a;
  --green-bar:#5fae1a;
  --chip:#ececec;
  --track:#e4ebf5;
  --line:#ececec;
  --nav:#000000;
  --purple:#8a7ad8;
}
*{box-sizing:border-box;margin:0;padding:0}
html,body{width:1200px;height:1140px;overflow:hidden;background:var(--page);font-family:"Poppins",sans-serif;color:var(--text)}
.stage{position:absolute;left:0;top:0;width:1464px;height:1391px;transform:scale(.8197);transform-origin:0 0}
.phone{position:absolute;top:63px;width:414px;overflow:hidden;background:var(--white)}
.phone--home{left:66px;height:1266px;background:linear-gradient(200deg,#fff 70%,#dfe9f7 88%,#9bbbe6 100%)}
.phone--summary{left:525px;height:995px;background:linear-gradient(200deg,#fff 72%,#e3ecf8 86%,#a9c4ea 100%)}
.phone--total{left:984px;height:995px;background:linear-gradient(200deg,#fff 72%,#e3ecf8 86%,#a9c4ea 100%)}
.abs{position:absolute}
.header{position:absolute;left:0;top:0;width:414px;height:240px}
.brand{position:absolute;top:122px;left:0;width:414px;text-align:center;font-weight:800;font-size:36px;color:var(--blue);letter-spacing:.5px}
.top-icon{position:absolute;top:26px;width:32px;height:32px;border-radius:50%;background:var(--white);display:flex;align-items:center;justify-content:center}
.section-title{position:absolute;left:33px;font-weight:600;font-size:16px;color:var(--muted);display:flex;align-items:center;gap:12px;width:346px}
.section-title::after{content:"";flex:1;height:1px;background:var(--blue)}
.chip{position:absolute;height:28px;background:var(--chip);border-radius:3px;font-size:10.5px;color:var(--muted);display:flex;align-items:center;justify-content:space-between;padding:0 9px}
.chip svg{width:8px;height:8px}
.stat-card{position:absolute;top:204px;width:162px;height:96px;background:var(--white);border-radius:14px;box-shadow:0 4px 14px rgba(0,0,0,.08);padding:24px 0 0 19px}
.stat-card .label{font-size:17px;color:var(--muted)}
.stat-card .value{font-size:26px;font-weight:700;color:var(--ink);margin-top:2px}
.stat-card svg{position:absolute;right:14px;top:12px}
.metric{position:absolute;left:34px;width:355px}
.metric .row{display:flex;justify-content:space-between;font-size:13.5px;color:var(--text)}
.metric .row b{font-weight:600;font-size:14.5px}
.metric .track{margin-top:14px;width:344px;height:7px;background:var(--track)}
.metric .fill{height:7px;background:var(--blue)}
.btn-next{position:absolute;left:34px;width:346px;height:54px;border-radius:27px;background:var(--green);color:var(--white);font-weight:700;font-size:17px;letter-spacing:.5px;display:flex;align-items:center;justify-content:center;gap:14px}
.nav{position:absolute;left:0;width:414px;height:62px;background:var(--nav);border-radius:30px 30px 0 0;overflow:hidden;display:flex}
.nav .tab{width:73px;height:62px;display:flex;align-items:center;justify-content:center}
.nav .tab:first-child{width:97px;padding-left:24px}
.nav .tab.active{background:var(--blue)}
.nav svg{width:28px;height:28px;fill:var(--white)}
.page-title{position:absolute;font-weight:700;font-size:28px;color:var(--ink);letter-spacing:.5px}
.detail-card{position:absolute;left:25px;top:339px;width:365px;height:477px;background:var(--white);border-radius:18px;box-shadow:0 4px 18px rgba(0,0,0,.08);overflow:hidden}
.detail-row{display:flex;height:53px;border-bottom:1px solid var(--line);font-size:14.5px;align-items:stretch}
.detail-row:last-child{border-bottom:none}
.detail-row .k{width:227px;padding-left:23px;display:flex;align-items:center;color:var(--muted);border-right:1px solid var(--line)}
.detail-row .v{padding-left:30px;display:flex;align-items:center;font-weight:500;color:var(--text)}
.toggle{position:absolute;left:109px;top:332px;width:196px;height:42px;border:1.5px solid var(--green);border-radius:21px;display:flex;overflow:hidden;font-size:18px;font-weight:500}
.toggle span{flex:1;display:flex;align-items:center;justify-content:center;color:var(--green)}
.toggle .on{background:var(--green);color:var(--white)}
.period{position:absolute;top:412px;width:92px;height:42px;background:var(--chip);display:flex;align-items:center;justify-content:center;font-size:16px;color:var(--muted)}
.period.on{background:var(--blue);color:var(--white)}
.week{position:absolute;top:768px;font-size:13.5px;color:var(--muted);transform:translateX(-50%)}
.kpi{position:absolute;top:823px;width:88px;height:77px;background:var(--white);border-radius:10px;box-shadow:0 3px 10px rgba(0,0,0,.06);text-align:center;padding-top:17px}
.kpi b{display:block;font-size:18px;font-weight:700;color:var(--blue);line-height:1.1}
.kpi span{font-size:13px;color:var(--muted)}
</style>
</head>
<body>
<svg width="0" height="0" style="position:absolute">
  <defs>
    <linearGradient id="hdrGrad" x1="0" y1="0" x2="1" y2="0.3">
      <stop offset="0" stop-color="#3a7cc0"/>
      <stop offset=".5" stop-color="#3f8f7a"/>
      <stop offset="1" stop-color="#4fa36a"/>
    </linearGradient>
    <linearGradient id="hdrFade" x1="0" y1="0" x2="0" y2="1">
      <stop offset="0" stop-color="#cfe6d8" stop-opacity=".9"/>
      <stop offset="1" stop-color="#ffffff" stop-opacity="0"/>
    </linearGradient>
    <symbol id="header" viewBox="0 0 414 240">
      <rect width="414" height="240" fill="#fff"/>
      <path d="M0 55 C120 110 300 110 414 55 L414 240 L0 240Z" fill="url(#hdrFade)"/>
      <path d="M0 0 H414 V55 C300 110 120 110 0 55Z" fill="url(#hdrGrad)"/>
      <path d="M0 58 C120 113 300 113 414 58" fill="none" stroke="#1f5fae" stroke-width="3"/>
      <circle cx="207" cy="82" r="68" fill="#fff"/>
      <circle cx="207" cy="70" r="32" fill="#2f6fc4"/>
    </symbol>
    <symbol id="caret" viewBox="0 0 8 8"><path d="M1 2.5 L4 5.5 L7 2.5" fill="none" stroke="#555" stroke-width="1.3"/></symbol>
    <symbol id="user" viewBox="0 0 16 16"><circle cx="8" cy="5" r="3" fill="#2f6fc4"/><path d="M2.5 14 C3 9.5 13 9.5 13.5 14Z" fill="#2f6fc4"/></symbol>
    <symbol id="bell" viewBox="0 0 16 16"><path d="M8 2 C5 2 4 4.5 4 7 V10 L2.5 12 H13.5 L12 10 V7 C12 4.5 11 2 8 2Z" fill="#2f6fc4"/><circle cx="8" cy="13.5" r="1.6" fill="#2f6fc4"/></symbol>
    <symbol id="i-home" viewBox="0 0 28 28"><path d="M14 3 L26 14 H22.5 V25 H17 V18 H11 V25 H5.5 V14 H2Z"/></symbol>
    <symbol id="i-loan" viewBox="0 0 28 28"><path d="M14 2 L24 10 H21 V16 H7 V10 H4Z"/><text x="14" y="14.5" font-size="7" font-weight="700" text-anchor="middle" fill="#000" font-family="Poppins,sans-serif">%</text><path d="M2 18 H8 L13 21 H19 C21 21 21 24 19 24 H12 V25 H21 L26 21 V26 H2Z"/></symbol>
    <symbol id="i-doc" viewBox="0 0 28 28"><path d="M4 2 H17 L21 6 V13 L15 20 L14 25 H4Z"/><path d="M7 8 H16 M7 12 H16 M7 16 H13" stroke="#000" stroke-width="1.6"/><path d="M24 11 L26.5 13.5 L18 22 L15 23 L16 20Z"/></symbol>
    <symbol id="i-chart" viewBox="0 0 28 28"><rect x="3" y="18" width="4" height="8"/><rect x="9" y="14" width="4" height="12"/><rect x="15" y="16" width="4" height="10"/><rect x="21" y="10" width="4" height="16"/><path d="M3 14 L10 8 L15 11 L24 3" fill="none" stroke="#fff" stroke-width="2"/><path d="M20 3 H25 V8Z"/></symbol>
    <symbol id="i-gear" viewBox="0 0 28 28"><path d="M12 2 H16 L16.7 5.3 L19.6 6.5 L22.4 4.6 L25.2 7.4 L23.3 10.2 L24.5 13.1 L27.8 13.8 V17.8 L24.5 18.5 L23.3 21.4 L25.2 24.2 L22.4 27 L19.6 25.1 L16.7 26.3 L16 29.6 H12 L11.3 26.3 L8.4 25.1 L5.6 27 L2.8 24.2 L4.7 21.4 L3.5 18.5 L.2 17.8 V13.8 L3.5 13.1 L4.7 10.2 L2.8 7.4 L5.6 4.6 L8.4 6.5 L11.3 5.3Z" transform="translate(0 -1.8) scale(1 .95)"/><circle cx="14" cy="14" r="4.5" fill="#000"/></symbol>
    <symbol id="arrow-circle" viewBox="0 0 16 16"><circle cx="8" cy="8" r="7" fill="#fff"/><path d="M4 8 H11 M8 5 L11 8 L8 11" fill="none" stroke="#4a9a6a" stroke-width="2"/></symbol>
  </defs>
</svg>

<main class="stage">

  <!-- Home dashboard -->
  <section class="phone phone--home">
    <svg class="header"><use href="#header"/></svg>
    <div class="brand">LoomKit</div>
    <div class="top-icon" style="left:306px"><svg width="16" height="16"><use href="#user"/></svg></div>
    <div class="top-icon" style="left:347px"><svg width="16" height="16"><use href="#bell"/></svg></div>

    <div class="stat-card" style="left:34px">
      <svg width="30" height="30" viewBox="0 0 30 30"><rect x="3" y="9" width="24" height="18" rx="2" fill="#2f6fc4"/><rect x="19" y="15" width="8" height="6" rx="1" fill="#fff"/><circle cx="10" cy="6" r="4" fill="#2f6fc4"/><circle cx="20" cy="5" r="3" fill="#2f6fc4"/></svg>
      <div class="label">Disbursed</div><div class="value">$30,000</div>
    </div>
    <div class="stat-card" style="left:208px">
      <svg width="30" height="30" viewBox="0 0 30 30"><rect x="2" y="2" width="7" height="7" fill="#2f6fc4"/><rect x="11" y="2" width="7" height="7" fill="#2f6fc4"/><rect x="20" y="2" width="7" height="7" fill="#2f6fc4"/><path d="M5 11 L14 19 M14 11 V19 M23 11 L14 19" stroke="#2f6fc4" stroke-width="1.5"/><ellipse cx="14" cy="22" rx="5" ry="2.5" fill="#2f6fc4"/><ellipse cx="14" cy="26" rx="5" ry="2.5" fill="#2f6fc4"/></svg>
      <div class="label">Collected</div><div class="value">$20,000</div>
    </div>
    <div class="stat-card" style="left:383px">
      <div class="label">Active</div><div class="value">20</div>
    </div>

    <div class="abs" style="left:34px;top:322px;width:380px;height:3px;background:#dde8e1"></div>
    <div class="abs" style="left:34px;top:322px;width:78px;height:3px;background:var(--green)"></div>

    <div class="section-title" style="top:357px">FILTERS:</div>
    <div class="chip" style="left:34px;top:399px;width:97px">Loan Officer<svg><use href="#caret"/></svg></div>
    <div class="chip" style="left:139px;top:399px;width:78px">Branch<svg><use href="#caret"/></svg></div>
    <div class="chip" style="left:225px;top:399px;width:66px">Fund<svg><use href="#caret"/></svg></div>
    <div class="chip" style="left:298px;top:399px;width:81px">Product<svg><use href="#caret"/></svg></div>

    <div class="metric" style="top:459px"><div class="row"><span>Near Due</span><b>$25,00,000</b></div><div class="track"><div class="fill" style="width:183px"></div></div></div>
    <div class="metric" style="top:524px"><div class="row"><span>Due</span><b>$34,000</b></div><div class="track"><div class="fill" style="width:83px"></div></div></div>
    <div class="metric" style="top:589px"><div class="row"><span>Over Due</span><b style="margin-right:-9px">$20,00,000</b></div><div class="track"><div class="fill" style="width:163px"></div></div></div>
    <div class="metric" style="top:654px"><div class="row"><span>Pending Disbursement</span><b>$30,000</b></div><div class="track"><div class="fill" style="width:72px"></div></div></div>
    <div class="metric" style="top:719px"><div class="row"><span>Active Loans</span><b>$20,000</b></div><div class="track"><div class="fill" style="width:42px"></div></div></div>

    <div class="section-title" style="top:802px">REPORTS:</div>

    <svg class="abs" style="left:40px;top:858px" width="340" height="215" viewBox="40 858 340 215" role="img" aria-label="Bar chart of monthly report totals">
      <path d="M53 1058 V870 M46 878 L53 866 L60 878" fill="none" stroke="#222" stroke-width="3"/>
      <path d="M53 1057 H360 M352 1050 L365 1057 L352 1064" fill="none" stroke="#222" stroke-width="3"/>
      <g fill="var(--blue-bright)">
        <rect x="72" y="977" width="27" height="64"/>
        <rect x="111" y="925" width="27" height="116"/>
        <rect x="150" y="940" width="27" height="101"/>
        <rect x="228" y="907" width="27" height="134"/>
        <rect x="267" y="952" width="27" height="89"/>
        <rect x="306" y="930" width="27" height="111"/>
      </g>
      <rect x="189" y="874" width="27" height="167" fill="var(--green-bar)"/>
      <polyline points="85,977 124,925 163,940 202,874 241,907 280,952 319,930" fill="none" stroke="#333" stroke-width="1.5" stroke-dasharray="2 3"/>
      <g fill="#e52b2b"><circle cx="85" cy="977" r="5"/><circle cx="124" cy="925" r="5"/><circle cx="163" cy="940" r="5"/><circle cx="202" cy="874" r="5"/><circle cx="241" cy="907" r="5"/><circle cx="280" cy="952" r="5"/><circle cx="319" cy="930" r="5"/></g>
    </svg>

    <div class="btn-next" style="top:1091px">NEXT <svg width="16" height="16"><use href="#arrow-circle"/></svg></div>

    <nav class="nav" style="top:1204px">
      <div class="tab active"><svg><use href="#i-home"/></svg></div>
      <div class="tab"><svg><use href="#i-loan"/></svg></div>
      <div class="tab"><svg><use href="#i-doc"/></svg></div>
      <div class="tab"><svg><use href="#i-chart"/></svg></div>
      <div class="tab"><svg><use href="#i-gear"/></svg></div>
    </nav>
  </section>

  <!-- Loan summary -->
  <section class="phone phone--summary">
    <svg class="header"><use href="#header"/></svg>
    <div class="brand">LoomKit</div>
    <div class="top-icon" style="left:306px"><svg width="16" height="16"><use href="#user"/></svg></div>
    <div class="top-icon" style="left:347px"><svg width="16" height="16"><use href="#bell"/></svg></div>

    <h1 class="page-title" style="left:33px;top:187px">LOAN SUMMARY</h1>
    <svg class="abs" style="left:353px;top:195px" width="26" height="26" viewBox="0 0 26 26"><circle cx="13" cy="13" r="13" fill="#3b8a8a"/><circle cx="12" cy="12" r="3" fill="none" stroke="#fff" stroke-width="1.6"/><path d="M14 14 L16.5 16.5" stroke="#fff" stroke-width="1.8"/></svg>

    <div class="section-title" style="top:240px">FILTERS:</div>
    <div class="chip" style="left:34px;top:282px;width:95px">Loan Officer<svg><use href="#caret"/></svg></div>
    <div class="chip" style="left:139px;top:282px;width:77px">Branch<svg><use href="#caret"/></svg></div>
    <div class="chip" style="left:225px;top:282px;width:66px">Fund<svg><use href="#caret"/></svg></div>
    <div class="chip" style="left:298px;top:282px;width:81px">Product<svg><use href="#caret"/></svg></div>

    <div class="detail-card">
      <div class="detail-row"><div class="k">Loan Reference Number :</div><div class="v">3213</div></div>
      <div class="detail-row"><div class="k">Loan Status :</div><div class="v">Active</div></div>
      <div class="detail-row"><div class="k">Date Disbursed :</div><div class="v">13/07/2024</div></div>
      <div class="detail-row"><div class="k">Date Approved :</div><div class="v">20/07/2024</div></div>
      <div class="detail-row"><div class="k">Last Repayment Date :</div><div class="v">27/07/2024</div></div>
      <div class="detail-row"><div class="k">Next Repayment Date :</div><div class="v">27/07/2024</div></div>
      <div class="detail-row"><div class="k">Amount Disbursed :</div><div class="v">30,000</div></div>
      <div class="detail-row"><div class="k">Amount Outstanding :</div><div class="v">30,000</div></div>
      <div class="detail-row"><div class="k">Overdue Days :</div><div class="v">15</div></div>
    </div>

    <div class="btn-next" style="top:851px">NEXT <svg width="16" height="16"><use href="#arrow-circle"/></svg></div>

    <nav class="nav" style="top:933px">
      <div class="tab"><svg><use href="#i-home"/></svg></div>
      <div class="tab active"><svg><use href="#i-loan"/></svg></div>
      <div class="tab"><svg><use href="#i-doc"/></svg></div>
      <div class="tab"><svg><use href="#i-chart"/></svg></div>
      <div class="tab"><svg><use href="#i-gear"/></svg></div>
    </nav>
  </section>

  <!-- Total loan -->
  <section class="phone phone--total">
    <svg class="header"><use href="#header"/></svg>
    <div class="brand">LoomKit</div>
    <div class="top-icon" style="left:306px"><svg width="16" height="16"><use href="#user"/></svg></div>
    <div class="top-icon" style="left:347px"><svg width="16" height="16"><use href="#bell"/></svg></div>

    <h1 class="page-title" style="left:0;width:414px;text-align:center;top:182px">TOTAL LOAN</h1>

    <div class="section-title" style="top:234px">FILTERS:</div>
    <div class="chip" style="left:34px;top:276px;width:97px">Loan Officer<svg><use href="#caret"/></svg></div>
    <div class="chip" style="left:139px;top:276px;width:78px">Branch<svg><use href="#caret"/></svg></div>
    <div class="chip" style="left:225px;top:276px;width:66px">Fund<svg><use href="#caret"/></svg></div>
    <div class="chip" style="left:298px;top:276px;width:81px">Product<svg><use href="#caret"/></svg></div>

    <div class="toggle"><span class="on">Profit</span><span>Loss</span></div>

    <div class="period" style="left:11px">Day</div>
    <div class="period" style="left:111px">Week</div>
    <div class="period on" style="left:211px">Month</div>
    <div class="period" style="left:311px">Year</div>

    <svg class="abs" style="left:0;top:480px" width="414" height="280" viewBox="0 480 414 280" role="img" aria-label="Interest trend line chart by week">
      <defs>
        <linearGradient id="areaFade" x1="0" y1="0" x2="0" y2="1">
          <stop offset="0" stop-color="#8a7ad8" stop-opacity=".55"/>
          <stop offset="1" stop-color="#8a7ad8" stop-opacity="0"/>
        </linearGradient>
        <pattern id="hatch" width="4" height="10" patternUnits="userSpaceOnUse"><rect width="1.2" height="10" fill="url(#areaFade)"/></pattern>
        <mask id="fadeMask"><rect x="0" y="480" width="414" height="280" fill="url(#maskGrad)"/></mask>
        <linearGradient id="maskGrad" x1="0" y1="0" x2="0" y2="1"><stop offset=".3" stop-color="#fff"/><stop offset="1" stop-color="#fff" stop-opacity="0"/></linearGradient>
      </defs>
      <path d="M46 490 V746 H383" fill="none" stroke="#d9d9d9" stroke-width="1"/>
      <path d="M52 720 C60 685 80 678 110 680 C140 682 150 690 175 678 C195 660 198 610 225 605 C250 600 260 625 282 618 C300 612 305 560 320 540 C335 525 350 525 368 525 V746 H52Z" fill="#a89be6" opacity=".55" mask="url(#fadeMask)" style="fill:url(#hatch)"/>
      <path d="M52 720 C60 685 80 678 110 680 C140 682 150 690 175 678 C195 660 198 610 225 605 C250 600 260 625 282 618 C300 612 305 560 320 540 C335 525 350 525 368 525" fill="none" stroke="var(--purple)" stroke-width="2"/>
      <path d="M363 526 V746" stroke="#4b55d6" stroke-width="2"/>
      <circle cx="360" cy="507" r="6" fill="#5a63d8"/><circle cx="360" cy="507" r="2.2" fill="#fff"/>
      <text x="342" y="507" text-anchor="end" font-family="Poppins,sans-serif" font-size="16" font-weight="600" fill="#1f1f1f">$ 35,00,000</text>
      <text x="342" y="527" text-anchor="end" font-family="Poppins,sans-serif" font-size="13" fill="#555">Interest</text>
    </svg>

    <div class="week" style="left:73px">Week 1</div>
    <div class="week" style="left:169px">Week 2</div>
    <div class="week" style="left:266px">Week 3</div>
    <div class="week" style="left:362px">Week 4</div>

    <div class="kpi" style="left:16px"><b>$300</b><span>Revenue</span></div>
    <div class="kpi" style="left:114px"><b>$350</b><span>Expenses</span></div>
    <div class="kpi" style="left:212px"><b>$200</b><span>Tax</span></div>
    <div class="kpi" style="left:310px"><b>$2000</b><span>Salaries</span></div>

    <nav class="nav" style="top:933px">
      <div class="tab"><svg><use href="#i-home"/></svg></div>
      <div class="tab"><svg><use href="#i-loan"/></svg></div>
      <div class="tab"><svg><use href="#i-doc"/></svg></div>
      <div class="tab active"><svg><use href="#i-chart"/></svg></div>
      <div class="tab"><svg><use href="#i-gear"/></svg></div>
    </nav>
  </section>

</main>
</body>
</html>
```